Maple9Tone

I need a website designed to feature a new product for my company. I am dedicating a separate site just highlight the program. The url will be maple9tone.com and the product name is maple tone. The product is ringless voicemail. We take a recorded script and send it to our clients customers cell phones without the phone ringing.

The site will consist of a home page. I animated video demo. It will house 18 scripts and voice overs to match, a results page, and a page to request a live demo.

We sell the product to new car dealerships

```html
<!DOCTYPE html>
<html lang="en">
<head>
<meta charset="utf-8">
<title>Maple9Tone – Fast, Effective, Inexpensive, Versatile Marketing</title>
<link href="https://fonts.googleapis.com/css2?family=Open+Sans:wght@300;400;600&display=swap" rel="stylesheet">
<style>
:root{
  --navy:#1f4e7d;
  --orange:#f58220;
  --text:#555b63;
  --heading:#333;
  --line:#e3e3e3;
  --panel:#f4f4f4;
  --white:#fff;
}
*{box-sizing:border-box;margin:0;padding:0}
html,body{width:1200px;height:2620px;overflow:hidden;background:var(--white)}
body{position:relative;font-family:"Open Sans",Arial,sans-serif;color:var(--text)}
.abs{position:absolute}

/* header */
.site-header{position:absolute;left:0;top:0;width:1200px;height:117px;background:var(--white)}
.brand{position:absolute;left:100px;top:26px;font-size:42px;font-weight:600;color:var(--navy);letter-spacing:-.5px;display:flex;align-items:center;gap:10px}
.brand-dot{width:14px;height:14px;border-radius:50%;background:var(--orange)}
.main-nav a{position:absolute;top:40px;height:35px;line-height:35px;font-size:13px;color:#444;text-decoration:none;transform:translateX(-50%);white-space:nowrap}
.main-nav a.is-active{background:var(--navy);color:var(--white);border-radius:18px;width:97px;text-align:center}

/* hero */
.hero{position:absolute;left:0;top:117px;width:1200px;height:557px;overflow:hidden}
.hero-photo{position:absolute;inset:0;background:radial-gradient(ellipse at 60% 55%,#e9e4df 0%,#c9bdb2 35%,#9d8e82 70%,#7e7066 100%)}
.hero-title{position:absolute;left:0;right:0;top:150px;text-align:center;color:var(--white);font-weight:300;font-size:92px;letter-spacing:1px;line-height:1}
.hero-sub{position:absolute;left:0;right:0;top:262px;text-align:center;color:var(--white);font-size:25px}
.hero-dots{position:absolute;left:562px;top:466px;display:flex;gap:4px}
.hero-dots span{width:16px;height:16px;border-radius:50%;background:var(--white)}
.hero-dots span.is-current{background:transparent;border:2px solid var(--white)}

/* section titles */
.section-title{position:absolute;left:0;right:0;text-align:center;font-weight:300;font-size:36px;color:var(--heading);letter-spacing:.5px}

/* how it works */
.steps{position:absolute;left:0;top:0;width:1200px;height:1310px;pointer-events:none}
.step{position:absolute;width:176px;height:176px;border-radius:50%;border:2px solid #ececec;background:var(--white);display:flex;flex-direction:column;align-items:center;justify-content:center;text-align:center;padding:0 22px}
.step svg{width:26px;height:26px;margin-bottom:10px}
.step p{font-size:11.5px;line-height:18px;color:var(--navy)}

/* video section */
.video-band{position:absolute;left:0;top:1310px;width:1200px;height:695px;background:var(--panel)}
.offer-title{position:absolute;left:100px;top:1455px;font-size:38px;font-weight:300;color:var(--navy)}
.offer-list{position:absolute;left:100px;top:1524px;width:560px;list-style:none}
.offer-list li{position:relative;padding-left:24px;font-size:14px;line-height:30px;color:#444}
.offer-list li svg{position:absolute;left:0;top:9px;width:13px;height:11px}
.script-title{position:absolute;left:100px;top:1700px;font-size:25px;font-weight:300;color:var(--navy)}
.script{position:absolute;left:100px;top:1757px;width:1000px;font-size:13.5px;line-height:26px;color:#444}
.script p{margin-bottom:4px}
.player{position:absolute;left:667px;top:1450px;width:433px;height:280px;background:var(--white);border:1px solid #d6d6d6;padding:10px;box-shadow:0 1px 3px rgba(0,0,0,.12)}
.player-screen{width:100%;height:225px;background:linear-gradient(135deg,#56b6e6,#3fa3d9)}
.player-bar{width:100%;height:33px;background:#333;position:relative}

/* clients */
.client{position:absolute;top:2143px;width:154px;height:70px;border:1px solid #e6e6e6;display:flex;align-items:center;justify-content:center;font-size:15px;font-weight:600;color:var(--navy);background:var(--white)}
.carousel-arrow{position:absolute;top:2165px;width:18px;height:26px}

/* footer */
.site-footer{position:absolute;left:0;top:2292px;width:1200px;height:328px;background:var(--panel)}
.footer-col{position:absolute;top:2336px}
.footer-col h4{font-size:14px;font-weight:400;color:var(--orange);margin-bottom:14px;letter-spacing:.3px}
.footer-col li{list-style:none;font-size:12.5px;line-height:30px;color:#444}
.footer-col .contact-line{display:flex;align-items:center;gap:10px}
.footer-col .contact-line svg{width:13px;height:13px}
.footer-divider{position:absolute;top:2336px;width:1px;height:185px;background:#dcdcdc}
.socials{display:flex;gap:7px;margin-top:14px}
.socials span{width:35px;height:35px;border-radius:50%}
.footer-rule{position:absolute;left:100px;top:2550px;width:1000px;height:1px;background:#cfcfcf}
.copyright{position:absolute;left:100px;top:2571px;font-size:11.5px;color:#444}
.page-code{position:absolute;right:100px;top:2571px;font-size:13px;color:#444}
</style>
</head>
<body>

<header class="site-header">
  <div class="brand">Maple9Tone<span class="brand-dot"></span></div>
  <nav class="main-nav">
    <a class="is-active" href="#" style="left:582px">HOME</a>
    <a href="#" style="left:706px">HOW IT WORKS</a>
    <a href="#" style="left:835px">OFFERS</a>
    <a href="#" style="left:940px">CLIENTS</a>
    <a href="#" style="left:1062px">CONTACT US</a>
  </nav>
</header>

<section class="hero">
  <div class="hero-photo" role="img" aria-label="Close-up of hands holding a white smartphone"></div>
  <h1 class="hero-title">MAPLE TONE</h1>
  <p class="hero-sub">Fast, Effective, Inexpensive, Versatile Marketing</p>
  <div class="hero-dots"><span class="is-current"></span><span></span><span></span><span></span></div>
</section>

<h2 class="section-title" style="top:718px">HOW IT WORKS</h2>

<svg class="steps" viewBox="0 0 1200 1310" aria-hidden="true">
  <defs>
    <marker id="arrowhead" markerWidth="8" markerHeight="8" refX="7" refY="4" orient="auto">
      <path d="M0,0 L7,4 L0,8" fill="none" stroke="#c9c9c9" stroke-width="1.2"/>
    </marker>
  </defs>
  <g stroke="#d6d6d6" stroke-width="1.5" fill="none" marker-end="url(#arrowhead)">
    <line x1="276" y1="905" x2="372" y2="905"/>
    <line x1="550" y1="905" x2="646" y2="905"/>
    <line x1="824" y1="905" x2="922" y2="905"/>
    <polyline points="1014,993 1014,1018 184,1018 184,1060"/>
    <line x1="276" y1="1153" x2="372" y2="1153"/>
    <line x1="550" y1="1153" x2="646" y2="1153"/>
    <line x1="824" y1="1153" x2="922" y2="1153"/>
  </g>
</svg>

<div class="step" style="left:99px;top:817px">
  <svg viewBox="0 0 24 24"><path d="M5 2h10l5 5v15H5z" fill="none" stroke="#f58220" stroke-width="2"/><path d="M8 11h8M8 15h8M8 19h5" stroke="#f58220" stroke-width="2"/></svg>
  <p>We select a targeted list of past sales customers, service customers, or unsold leads.</p>
</div>
<div class="step" style="left:373px;top:817px">
  <svg viewBox="0 0 24 24"><rect x="3" y="5" width="15" height="16" rx="2" fill="none" stroke="#f58220" stroke-width="2"/><path d="M10 14l10-10 2 2-10 10h-2z" fill="#f58220"/></svg>
  <p>We develop and record a script based on your stores current needs, incentives, time of year, and list.</p>
</div>
<div class="step" style="left:647px;top:817px">
  <svg viewBox="0 0 24 24"><circle cx="12" cy="6" r="3.5" fill="#f58220"/><circle cx="5" cy="9" r="2.8" fill="#f58220"/><circle cx="19" cy="9" r="2.8" fill="#f58220"/><path d="M6 21a6 6 0 0 1 12 0z" fill="#f58220"/><path d="M0 21a5 5 0 0 1 7-5v5zM24 21a5 5 0 0 0-7-5v5z" fill="#f58220"/></svg>
  <p>Your team will be coached and given a set of scripted responses to be sure everyone is prepared.</p>
</div>
<div class="step" style="left:923px;top:817px">
  <svg viewBox="0 0 24 24"><rect x="4" y="5" width="16" height="11" rx="1" fill="none" stroke="#f58220" stroke-width="2"/><path d="M1 19h22" stroke="#f58220" stroke-width="2.5"/></svg>
  <p>Your message and list are uploaded to our system and delivered at any speed you wish.</p>
</div>

<div class="step" style="left:99px;top:1065px">
  <svg viewBox="0 0 24 24"><rect x="1" y="1" width="22" height="22" rx="4" fill="#f58220"/><path d="M8 6l2 3-1.5 1.5a8 8 0 0 0 4 4L14 13l3 2-1 3c-5 0-10-5-10-10z" fill="#fff"/></svg>
  <p>Inbound return calls will begin within minutes.</p>
</div>
<div class="step" style="left:373px;top:1065px">
  <svg viewBox="0 0 24 24"><g fill="#f58220"><circle cx="12" cy="12" r="7"/><rect x="10" y="1" width="4" height="5"/><rect x="10" y="18" width="4" height="5"/><rect x="1" y="10" width="5" height="4"/><rect x="18" y="10" width="5" height="4"/><rect x="10" y="1" width="4" height="5" transform="rotate(45 12 12)"/><rect x="10" y="1" width="4" height="5" transform="rotate(135 12 12)"/><rect x="10" y="1" width="4" height="5" transform="rotate(225 12 12)"/><rect x="10" y="1" width="4" height="5" transform="rotate(315 12 12)"/></g><circle cx="12" cy="12" r="3" fill="#fff"/></svg>
  <p>This program requires zero set up.</p>
</div>
<div class="step" style="left:647px;top:1065px">
  <svg viewBox="0 0 24 24"><circle cx="12" cy="12" r="9.5" fill="none" stroke="#f58220" stroke-width="2.5"/><path d="M12 6v6h-4" fill="none" stroke="#f58220" stroke-width="2.5"/></svg>
  <p>The simple process above can be completed and go live in as little as 24 hours.</p>
</div>
<div class="step" style="left:923px;top:1065px">
  <svg viewBox="0 0 24 24"><g fill="none" stroke="#f58220" stroke-width="2.5"><path d="M9 5l3-3 3 3M12 2v7"/><path d="M20 11l1 4-4 1M21 15l-6-4"/><path d="M5 20l-4-1 1-4M1 19l6-3"/><path d="M8 9L4 15M16 9l3 5M8 20h9"/></g></svg>
  <p>Every inbound phone call is recorded, tracked, and caller id information is captured.</p>
</div>

<section class="video-band"></section>
<h2 class="section-title" style="top:1362px">OUR VIDEO</h2>

<h3 class="offer-title">The Offer</h3>
<ul class="offer-list">
  <li><svg viewBox="0 0 13 11"><path d="M1 6l4 4 7-9" fill="none" stroke="#f58220" stroke-width="2.4"/></svg>We can use this as a buy back offer, re-engage unsold CRM leads, offer monthly factory incentives, inform of a sales event, or to get CSI surveys completed</li>
  <li><svg viewBox="0 0 13 11"><path d="M1 6l4 4 7-9" fill="none" stroke="#f58220" stroke-width="2.4"/></svg>It can be recorded by anyone!</li>
  <li><svg viewBox="0 0 13 11"><path d="M1 6l4 4 7-9" fill="none" stroke="#f58220" stroke-width="2.4"/></svg>Works because the message is perfect every time!</li>
  <li><svg viewBox="0 0 13 11"><path d="M1 6l4 4 7-9" fill="none" stroke="#f58220" stroke-width="2.4"/></svg>The information stays with them!</li>
</ul>

<h3 class="script-title">Sample Script:</h3>
<div class="script">
  <p>Hi this is (Managers Name), I'm the (Title) at (Dealership). I have a customer that's interested in a car like the one you purchased from us and I'm hoping you would be interested in allowing us to buy it back from you?</p>
  <p>I'd be willing to pay you up to 125% of Harlow Value Guide for that vehicle.</p>
  <p>It's somewhat urgent, so if you are interested, please call me back right away. Also, if you decide you'd like to replace it, or if you're interested in buying something else, I'm willing to give you a huge discount on a new or pre-owned vehicle of your choice!</p>
  <p>Again, this is (Managers First Name) at (Dealership) - my number is (our tracking number to be added). Talk to you soon. Bye</p>
</div>

<div class="player">
  <div class="player-screen" role="img" aria-label="Animated demo video still: cartoon presenter beside a smartphone with the Maple Tone title"></div>
  <div class="player-bar">
    <svg width="413" height="33" viewBox="0 0 413 33" aria-hidden="true">
      <path d="M14 10l10 6.5-10 6.5z" fill="#fff"/>
      <rect x="40" y="15" width="300" height="4" rx="2" fill="#ddd"/>
      <rect x="40" y="15" width="110" height="4" rx="2" fill="#3fa3d9"/>
      <path d="M380 13h4l5-4v15l-5-4h-4z" fill="#fff"/>
      <path d="M392 12a6 6 0 0 1 0 9" fill="none" stroke="#fff" stroke-width="1.5"/>
    </svg>
  </div>
</div>

<h2 class="section-title" style="top:2052px">OUR CLIENTS</h2>
<svg class="carousel-arrow" style="left:54px" viewBox="0 0 18 26" aria-hidden="true"><path d="M14 2L4 13l10 11" fill="none" stroke="#c8c8c8" stroke-width="3"/></svg>
<div class="client" style="left:100px">Redfern Motors</div>
<div class="client" style="left:270px">Lakeside Autos</div>
<div class="client" style="left:439px">Northgate Cars</div>
<div class="client" style="left:609px">Carver</div>
<div class="client" style="left:778px">Halden</div>
<div class="client" style="left:948px">Brisk Advertising</div>
<svg class="carousel-arrow" style="left:1128px" viewBox="0 0 18 26" aria-hidden="true"><path d="M4 2l10 11-10 11" fill="none" stroke="#c8c8c8" stroke-width="3"/></svg>

<footer class="site-footer"></footer>
<div class="footer-col" style="left:100px"><h4>COMPANY</h4><ul><li>Home</li><li>How it Works</li><li>Offers</li><li>Clients</li><li>Contact Us</li></ul></div>
<div class="footer-divider" style="left:233px"></div>
<div class="footer-col" style="left:274px"><h4>REFERENCES</h4><ul><li>Dale Morrow</li><li>TJ (Thomas Ellery)</li><li>Walter Brenning</li><li>Paul Devane</li><li>Others</li></ul></div>
<div class="footer-divider" style="left:452px"></div>
<div class="footer-col" style="left:498px"><h4>GET IN TOUCH</h4><ul>
  <li class="contact-line"><svg viewBox="0 0 24 24"><path d="M5 2l4 5-2.5 2.5a12 12 0 0 0 8 8L17 15l5 4-2 4C10 23 1 14 1 4z" fill="#333"/></svg>Call us on 303 555 0147</li>
  <li class="contact-line"><svg viewBox="0 0 24 24"><rect x="1" y="4" width="22" height="16" fill="#333"/><path d="M1 5l11 8 11-8" fill="none" stroke="#f4f4f4" stroke-width="2"/></svg>pdevane@devanemarketing.com</li>
</ul></div>
<div class="footer-divider" style="left:729px"></div>
<div class="footer-col" style="left:769px"><h4>WHY US</h4><ul><li>Customers</li><li>Team</li><li>FAQ</li><li>Privacy Policy</li></ul></div>
<div class="footer-divider" style="left:885px"></div>
<div class="footer-col" style="left:926px"><h4>FOLLOW US</h4><ul><li>Please connect with us on</li></ul>
  <div class="socials"><span style="background:#3aa3dc"></span><span style="background:#2f5797"></span><span style="background:#1b6da8"></span><span style="background:#d8452f"></span></div>
</div>
<div class="footer-rule"></div>
<p class="copyright">© 2016 Company Name&nbsp; All right reserved&nbsp; Term of Use</p>
<p class="page-code">C16</p>

</body>
</html>
```